Business Card Design - Property Management & Real Estate Services

I need a business card design for my company that I can print ZEPLA Cards. The company is called Brindle Management Company. It is a property management and real estate company. The design has to be clean and modern. I need two versions. One for my employee and one for me. However, the design will be the same, just different text. You can get a feel for the company by looking at our website at www.brindlemanagement.example.

Industry/Entity Type

Property Management

Contact Information for Business Card

I will be using ZEPLA.com to print my cards. I will most likely use the rounded edges card. I need two versions, however, they will be the same design. I need one for me and my employee.

Colors
3276b5
33a6d7

Requirements
Must have
• Company Logo
• Name of person
• Property Management & Real Estate Service
• Phone
• Email
• Website
• Address
• A space to place a QR code

```html
<!DOCTYPE html>
<html lang="en">
<head>
<meta charset="utf-8">
<title>Brindle Management – Business Card</title>
<link rel="stylesheet" href="https://fonts.googleapis.com/css2?family=Exo+2:ital,wght@0,700&family=Roboto:wght@400;500&display=swap">
<style>
  :root {
    --backdrop: #3b3b3d;
    --card-black: #1d1e21;
    --brand-blue: #1f5aa6;
    --accent-blue: #6aa2e0;
    --logo-blue: #3276b5;
    --foil-silver: #a9acb1;
    --ink-white: #ffffff;
  }
  * { box-sizing: border-box; margin: 0; padding: 0; }
  html, body { width: 799px; height: 1200px; overflow: hidden; }
  body {
    background: var(--backdrop);
    font-family: "Roboto", Arial, sans-serif;
    position: relative;
  }
  .card {
    position: absolute;
    left: 80px;
    width: 640px;
    height: 366px;
    border-radius: 26px;
    background: var(--card-black);
    overflow: hidden;
  }
  .card--front { top: 150px; }
  .card--back { top: 690px; }

  .brand-name {
    position: absolute;
    font-family: "Roboto", Arial, sans-serif;
    font-weight: 500;
    text-transform: uppercase;
    letter-spacing: 4px;
    white-space: nowrap;
  }
  .card--front .brand-name {
    left: 0; right: 0; top: 160px;
    text-align: center;
    font-size: 30px;
    color: var(--foil-silver);
  }
  .card--back .brand-name {
    left: 40px; top: 70px;
    font-size: 22px;
    color: var(--logo-blue);
  }
  .brand-mark {
    position: absolute;
    background: var(--logo-blue);
    width: 12px; height: 12px;
    left: 40px; top: 50px;
  }

  .wave { position: absolute; left: 0; top: 0; width: 640px; height: 366px; }

  .contact {
    position: absolute;
    right: 34px; top: 200px;
    text-align: right;
    color: var(--ink-white);
  }
  .contact__name {
    font-family: "Exo 2", Arial, sans-serif;
    font-weight: 700;
    font-size: 24px;
    line-height: 1.1;
  }
  .contact__role { font-size: 16px; margin-bottom: 10px; }
  .contact__line {
    font-size: 15.5px;
    line-height: 1.45;
    display: flex;
    justify-content: flex-end;
    align-items: center;
    gap: 10px;
  }
  .contact__icon { width: 14px; height: 14px; flex: none; }
</style>
</head>
<body>

  <section class="card card--front" aria-label="Card front">
    <span class="brand-name">Brindle Management</span>
  </section>

  <section class="card card--back" aria-label="Card back">
    <span class="brand-mark"></span>
    <span class="brand-name">Brindle Management</span>

    <svg class="wave" viewBox="0 0 640 366" aria-hidden="true">
      <path d="M0 170 C150 185 260 215 380 200 C480 188 560 160 640 145 L640 366 L0 366 Z" fill="var(--accent-blue)"/>
      <path d="M0 178 C150 195 260 228 380 212 C480 200 560 172 640 158 L640 366 L0 366 Z" fill="#0f1013"/>
      <path d="M0 200 C160 205 260 245 380 232 C480 222 560 192 640 175 L640 366 L0 366 Z" fill="var(--brand-blue)"/>
    </svg>

    <div class="contact">
      <p class="contact__name">Marisol T. Ortega</p>
      <p class="contact__role">Founder</p>
      <p class="contact__line">(555) 014-2837
        <svg class="contact__icon" viewBox="0 0 16 16"><path fill="#fff" d="M3 2h3l1 3-2 1.5a9 9 0 0 0 4.5 4.5L11 9l3 1v3a1 1 0 0 1-1 1A12 12 0 0 1 2 3a1 1 0 0 1 1-1z"/></svg>
      </p>
      <p class="contact__line">marisol@brindlemanagement.example
        <svg class="contact__icon" viewBox="0 0 16 16"><rect x="1" y="3" width="14" height="10" fill="#fff"/><path d="M1 3l7 6 7-6" fill="none" stroke="var(--brand-blue)" stroke-width="1.4"/></svg>
      </p>
      <p class="contact__line">www.brindlemanagement.example
        <svg class="contact__icon" viewBox="0 0 16 16"><circle cx="8" cy="8" r="6.5" fill="none" stroke="#fff" stroke-width="1.5"/><path d="M1.5 8h13M8 1.5c-3 3.5-3 9.5 0 13M8 1.5c3 3.5 3 9.5 0 13" fill="none" stroke="#fff" stroke-width="1.2"/></svg>
      </p>
      <p class="contact__line">4870 Harbor Ave #210 Lakeview, FL 30000</p>
    </div>
  </section>

</body>
</html>
```